Oil Field Service company needs professional business cards

Looking to clean up our current company business cards and look a little more professional. Brenwick Casing Services is a US based company that services the oil field. We deal with engineers, managers and oil rigs....................................................................................................................................................................................................................................................................................................................................................................................................

Target Market(s)

Oil and Gas professionals

Industry/Entity Type

Oil And Gas

Contact Information for Business Card

See attached photo as example

Font styles to use
Sans Serif

Colors
ec1f27

Requirements
Must have
• Company Logo, Name, Title, Cell, Office, Fax, Email.
• See attached photo
Nice to have
• External CRT, Internal CRT, Casing Crews, Torque Turn, Laydown Machine
Should not have
• Do not introduce any new pictures and keep it professional looking

```html
<!DOCTYPE html>
<html lang="en">
<head>
<meta charset="utf-8">
<title>Brenwick Casing Services – Business Cards</title>
<link href="https://fonts.googleapis.com/css2?family=Open+Sans:wght@400;600;700&display=swap" rel="stylesheet">
<style>
  :root {
    --brand-red: #ec1f27;
    --card-black: #030303;
    --steel-grey: #4b5661;
    --text-white: #ffffff;
    --page-bg: #e9e7e4;
  }
  * { margin: 0; padding: 0; box-sizing: border-box; }
  html, body {
    width: 1200px; height: 900px; overflow: hidden;
    background: var(--page-bg);
    font-family: "Open Sans", Arial, sans-serif;
  }
  .canvas { position: relative; width: 1200px; height: 900px; }

  .card {
    position: absolute;
    background: var(--card-black);
    overflow: hidden;
    box-shadow: 0 6px 18px rgba(0,0,0,.18);
  }
  .card-front { left: 78px; top: 35px; width: 588px; height: 364px; }
  .card-back  { left: 388px; top: 505px; width: 566px; height: 352px; }

  .front-bands { position: absolute; inset: 0; }

  .wordmark {
    position: absolute; left: 0; right: 0;
    display: flex; align-items: center; justify-content: center; gap: 12px;
    color: var(--steel-grey);
    font-weight: 700;
    text-transform: uppercase;
    letter-spacing: 3px;
    white-space: nowrap;
  }
  .wordmark-dot {
    width: 18px; height: 18px; border-radius: 50%;
    background: var(--brand-red); flex: none;
  }
  .card-front .wordmark { top: 92px; font-size: 27px; }
  .card-back .wordmark  { top: 150px; font-size: 26px; }

  .holder {
    position: absolute; right: 317px; top: 258px;
    text-align: right; color: var(--text-white);
  }
  .holder-name  { font-size: 20px; font-weight: 700; line-height: 28px; }
  .holder-title { font-size: 16px; line-height: 20px; }

  .contact-list {
    position: absolute; left: 296px; top: 249px;
    list-style: none; color: var(--text-white);
    font-size: 15px; line-height: 21px;
  }
  .contact-list li { display: flex; align-items: center; gap: 10px; }
  .contact-list svg { width: 12px; height: 12px; fill: var(--text-white); flex: none; }

  .footer-line {
    position: absolute; left: 59px; top: 320px;
    display: flex; align-items: center;
    color: var(--text-white); font-size: 15px; line-height: 22px;
  }
  .footer-divider { margin: 0 18px 0 22px; }
  .footer-line strong { font-weight: 700; margin-right: 5px; }

  .service-list {
    position: absolute; left: 0; right: 0; top: 266px;
    display: flex; flex-wrap: wrap; justify-content: center;
    column-gap: 14px; row-gap: 8px;
    padding: 0 100px;
    list-style: none; color: var(--text-white);
    font-size: 15px; line-height: 22px;
  }
  .service-list li { display: flex; align-items: center; gap: 10px; }
  .service-list li::before {
    content: ""; width: 7px; height: 7px; border-radius: 50%;
    background: var(--brand-red);
  }
</style>
</head>
<body>
<main class="canvas">

  <section class="card card-front" aria-label="Business card front">
    <svg class="front-bands" viewBox="0 0 588 364" width="588" height="364" aria-hidden="true">
      <polygon points="0,198 406,198 383,225 0,225" fill="var(--steel-grey)"/>
      <polygon points="0,228 383,228 414,190 588,190 588,364 0,364" fill="var(--brand-red)"/>
    </svg>

    <div class="wordmark"><span class="wordmark-dot"></span>Brenwick Casing Services</div>

    <div class="holder">
      <p class="holder-name">Cody Halvorsen</p>
      <p class="holder-title">Area Manager</p>
    </div>

    <ul class="contact-list">
      <li>
        <svg viewBox="0 0 24 24"><path d="M6.6 10.8a15 15 0 0 0 6.6 6.6l2.2-2.2c.3-.3.7-.4 1-.2 1.1.4 2.3.6 3.6.6.6 0 1 .4 1 1V20c0 .6-.4 1-1 1A17 17 0 0 1 3 4c0-.6.4-1 1-1h3.5c.6 0 1 .4 1 1 0 1.3.2 2.5.6 3.6.1.3 0 .7-.2 1z"/></svg>
        (555) 210-4800
      </li>
      <li>
        <svg viewBox="0 0 24 24"><path d="M2 5h20v14H2z M3.5 6.5 12 13l8.5-6.5" fill="var(--text-white)" stroke="var(--brand-red)" stroke-width="1.8"/></svg>
        (555) 210-4831
      </li>
      <li>
        <svg viewBox="0 0 24 24"><circle cx="12" cy="12" r="9.5" fill="none" stroke="var(--text-white)" stroke-width="2"/><path d="M2.5 12h19M12 2.5c3 3 3 16 0 19M12 2.5c-3 3-3 16 0 19" fill="none" stroke="var(--text-white)" stroke-width="1.6"/></svg>
        (555) 387-2619
      </li>
    </ul>

    <p class="footer-line">
      <span>Alder Creek,OK 73000</span>
      <span class="footer-divider">|</span>
      <strong>E:</strong><span>codyhalvorsen@brenwickcasing.com</span>
    </p>
  </section>

  <section class="card card-back" aria-label="Business card back">
    <div class="wordmark"><span class="wordmark-dot"></span>Brenwick Casing Services</div>
    <ul class="service-list">
      <li>External CRT</li>
      <li>Internal CRT</li>
      <li>Casing Crews</li>
      <li>Torque Turn</li>
      <li>Laydown Machine</li>
    </ul>
  </section>

</main>
</body>
</html>
```